BOLD & MINIMALIST DESIGN NEEDED

We want a very bold but minimalistic business card design that is impactful and utilizes both sides of the business card. Our current logo is included for your use.

We want bold fonts and good use of negative space. We don't want the logo to overpower the design.

Target Market(s)

Professionals who are building new commercial buildings.

Industry/Entity Type

Construction

Contact Information for Business Card

Name, Title, email, office phone, cell phone, website

Font styles to use
Serif
Sans Serif

Requirements
Must have
• Bold design!

```html
<!DOCTYPE html>
<html lang="en">
<head>
<meta charset="utf-8">
<title>Ridgeline Design + Build — Business Card</title>
<link rel="stylesheet" href="https://fonts.googleapis.com/css2?family=Montserrat:wght@400;700;800&display=swap">
<style>
  :root {
    --stage: #dcdcdc;
    --ink: #0c0d0f;
    --paper: #ffffff;
    --green: #8cc63f;
    --grey-text: #6a6a6a;
    --icon: #1a1a1a;
  }
  * { box-sizing: border-box; margin: 0; padding: 0; }
  html, body {
    width: 1200px; height: 1200px; overflow: hidden;
    background: var(--stage);
    font-family: "Montserrat", Arial, sans-serif;
  }
  .stage { position: relative; width: 1200px; height: 1200px; }
  .card {
    position: absolute; left: 179px; width: 862px; height: 496px; overflow: hidden;
  }
  .card--front { top: 84px; background: var(--ink); }
  .card--back { top: 621px; background: var(--paper); }

  .wordmark {
    position: absolute; display: flex; align-items: center; gap: 14px;
    color: var(--paper); font-weight: 800; text-transform: uppercase;
    white-space: nowrap; letter-spacing: 0.04em;
  }
  .wordmark__square { width: 22px; height: 22px; background: var(--green); flex: none; }
  .card--front .wordmark {
    left: 50%; top: 50%; transform: translate(-50%, -50%); font-size: 34px;
  }
  .card--back .wordmark { right: 52px; bottom: 58px; font-size: 24px; z-index: 2; }
  .card--back .wordmark__square { width: 16px; height: 16px; }

  .swoosh { position: absolute; inset: 0; width: 100%; height: 100%; }

  .person { position: absolute; left: 29px; top: 38px; }
  .person__name { font-size: 37px; font-weight: 700; color: var(--ink); line-height: 1.1; }
  .person__title { font-size: 28px; font-weight: 400; color: var(--green); letter-spacing: 0.03em; margin-top: 2px; }

  .contacts { position: absolute; left: 29px; top: 198px; list-style: none; }
  .contacts__item {
    display: flex; align-items: center; gap: 13px; height: 35px;
    font-size: 22px; color: var(--grey-text); letter-spacing: 0.04em;
  }
  .contacts__icon { width: 26px; height: 26px; flex: none; fill: var(--icon); }
  .contacts__accent { color: var(--green); }
</style>
</head>
<body>
<main class="stage">
  <section class="card card--front" aria-label="Card front">
    <div class="wordmark"><span class="wordmark__square"></span>Ridgeline Design + Build</div>
  </section>

  <section class="card card--back" aria-label="Card back">
    <svg class="swoosh" viewBox="0 0 1387 798" preserveAspectRatio="none" aria-hidden="true">
      <polygon fill="var(--ink)" points="0,556 312,722 1387,134 1387,798 0,798"/>
      <polygon fill="var(--green)" points="2,548 312,678 1302,172 312,712"/>
    </svg>

    <div class="person">
      <h1 class="person__name">Name Surename</h1>
      <p class="person__title">Director</p>
    </div>

    <ul class="contacts">
      <li class="contacts__item">
        <svg class="contacts__icon" viewBox="0 0 24 24"><path d="M6.6 10.8a15.1 15.1 0 0 0 6.6 6.6l2.2-2.2a1 1 0 0 1 1-.25 11.4 11.4 0 0 0 3.6.57 1 1 0 0 1 1 1V20a1 1 0 0 1-1 1A17 17 0 0 1 3 4a1 1 0 0 1 1-1h3.5a1 1 0 0 1 1 1c0 1.25.2 2.45.57 3.57a1 1 0 0 1-.25 1z"/></svg>
        555-014-2290
      </li>
      <li class="contacts__item">
        <svg class="contacts__icon" viewBox="0 0 24 24"><path d="M2 8c0-2 4.5-4 10-4s10 2 10 4v2h-5V8H7v2H2z"/><path d="M6 12h12l2 9H4zm6 2.5a2.5 2.5 0 1 0 0 5 2.5 2.5 0 0 0 0-5z"/></svg>
        555-014-2290
      </li>
      <li class="contacts__item">
        <svg class="contacts__icon" viewBox="0 0 24 24"><path d="M2 5h20v14H2zm2 2v.4l8 6 8-6V7zm0 2.9V17h4.6zm16 0L15.4 17H20zM10 14.4 5.6 17h12.8L14 14.4l-2 1.5z"/></svg>
        info@rdb-build.com
      </li>
      <li class="contacts__item">
        <svg class="contacts__icon" viewBox="0 0 24 24"><path d="M12 2a10 10 0 1 0 0 20 10 10 0 0 0 0-20zm-1 2.1V8H7.6A8 8 0 0 1 11 4.1zm2 0A8 8 0 0 1 16.4 8H13zM6.8 10H11v3H6.4a8 8 0 0 1 .4-3zm6.2 0h4.2a8 8 0 0 1 .4 3H13zm-6.6 5H11v4.9A8 8 0 0 1 6.4 15zm6.6 0h4.6a8 8 0 0 1-4.6 4.9z"/></svg>
        <span>www.<span class="contacts__accent">rdb-build</span>.com</span>
      </li>
    </ul>

    <div class="wordmark"><span class="wordmark__square"></span>Ridgeline Design + Build</div>
  </section>
</main>
</body>
</html>
```